Marwick Family Chiropractic Stationary

The letterhead and business card must have our logo.
We would like to see the logo used in different ways ( It can be expanded upon in the stationary.)
Please use the the same or similar colors.
Must be eye catching and memorable.
Must be easy to read

Reason: The doctor has been too busy to make any final decisions. He would like to give himself a little more time.

Target Market(s)

Chiropractic Healthcare

Industry/Entity Type

Business

Requirements
Must have
• Dr. Leonard Marwick D.C.
Chiropractor

860-555-0183

417 Birchfield Road, 2nd Floor
Vernon, CT 06091

drmarwick@marwickspine.example
www.marwickspine.example
www.facebook.com/MarwickFamilySpine
Should not have
• should not be difficult to read

```html
<!DOCTYPE html>
<html lang="en">
<head>
<meta charset="utf-8">
<title>Marwick Family Chiropractic – Business Card Set</title>
<link rel="stylesheet" href="https://fonts.googleapis.com/css2?family=Montserrat:wght@700&family=Source+Sans+3:ital,wght@0,400;0,600;0,700;1,700&display=swap">
<style>
  :root {
    --backdrop: #e8e3dc;
    --label: #2a2420;
    --card-white: #ffffff;
    --card-brown: #221b15;
    --card-black: #070707;
    --brand-green: #2a9a47;
    --brand-lime: #9ccc5a;
    --ink: #3a3a3a;
    --ink-soft: #555555;
    --on-dark: #f4f4f4;
    --shadow: 0 6px 16px rgba(0,0,0,0.28);
  }
  * { margin: 0; padding: 0; box-sizing: border-box; }
  html, body { width: 1200px; height: 788px; overflow: hidden; }
  body {
    position: relative;
    background: var(--backdrop);
    font-family: "Source Sans 3", "Helvetica Neue", Arial, sans-serif;
    color: var(--ink);
  }
  .view-label {
    position: absolute;
    width: 525px;
    text-align: center;
    font-size: 21px;
    color: var(--label);
  }
  .card {
    position: absolute;
    width: 525px;
    height: 298px;
    border-radius: 22px;
    overflow: hidden;
    box-shadow: var(--shadow);
    text-align: center;
  }
  .card--front { left: 55px; top: 78px; background: var(--card-white); }
  .card--back-light { left: 622px; top: 75px; background: var(--card-white); }
  .card--back-brown { left: 54px; top: 446px; background: var(--card-brown); }
  .card--back-black { left: 622px; top: 446px; background: var(--card-black); }

  .brand-name, .brand-line {
    font-family: "Montserrat", "Arial Black", sans-serif;
    font-weight: 700;
    text-transform: uppercase;
    position: absolute;
    left: 0; right: 0;
    line-height: 1;
  }
  .brand-mark {
    position: absolute;
    left: 50%;
    border-radius: 50%;
  }

  /* Front */
  .card--front .brand-name { top: 36px; font-size: 46px; color: var(--brand-green); }
  .card--front .brand-line { top: 84px; font-size: 18px; color: var(--brand-green); letter-spacing: 0.5px; }
  .contact-list {
    position: absolute;
    top: 128px; left: 0; right: 0;
    list-style: none;
    font-size: 13.5px;
    line-height: 22.5px;
    color: var(--ink-soft);
  }
  .contact-list .field { font-weight: 700; font-style: italic; color: var(--ink); }
  .rule {
    position: absolute;
    left: 0; right: 0; top: 255px;
    height: 2px;
    background: var(--brand-green);
  }
  .name-band {
    position: absolute;
    left: 0; right: 0; top: 262px; bottom: 0;
    background: var(--brand-green);
    color: #ffffff;
    font-weight: 700;
    font-size: 15px;
    line-height: 36px;
  }
  .name-band .role { font-size: 12.5px; }

  /* Back 1 */
  .card--back-light .brand-mark { top: 42px; width: 96px; height: 96px; margin-left: -48px; background: var(--brand-green); }
  .card--back-light .brand-name { top: 166px; font-size: 34px; color: var(--brand-green); }
  .card--back-light .brand-line { top: 206px; font-size: 14px; color: var(--brand-green); }

  .web {
    position: absolute;
    left: 0; right: 0; bottom: 20px;
    font-size: 15px;
  }
  .card--back-light .web { color: var(--ink); }
  .card--back-brown .web, .card--back-black .web { color: var(--on-dark); }

  /* Back 2 */
  .card--back-brown .brand-name { top: 96px; font-size: 66px; color: var(--brand-green); }
  .card--back-brown .brand-line { top: 168px; font-size: 26px; color: var(--brand-green); letter-spacing: 0.5px; }

  /* Back 3 */
  .card--back-black .brand-mark { top: 34px; width: 100px; height: 100px; margin-left: -50px; background: var(--brand-lime); }
  .card--back-black .brand-name { top: 170px; font-size: 32px; color: var(--brand-lime); }
  .card--back-black .brand-line { top: 208px; font-size: 14px; color: var(--brand-lime); }
</style>
</head>
<body>
  <div class="view-label" style="left:55px; top:34px;">Front</div>
  <div class="view-label" style="left:622px; top:34px;">Back - 1</div>
  <div class="view-label" style="left:54px; top:404px;">Back - 2</div>
  <div class="view-label" style="left:622px; top:404px;">Back - 3</div>

  <section class="card card--front">
    <div class="brand-name">Marwick</div>
    <div class="brand-line">Family Chiropractic</div>
    <ul class="contact-list">
      <li><span class="field">phone</span> 860-555-0183</li>
      <li><span class="field">email</span> mymarwick@marwickspine.example</li>
      <li><span class="field">web</span> : www.marwickspine.example</li>
      <li><span class="field">face book</span> : MarwickFamilySpine</li>
      <li>417 Birchfield Road, 2nd Floor, Vernon, CT 06091</li>
    </ul>
    <div class="rule"></div>
    <div class="name-band">Dr. Leonard Marwick D.C. - <span class="role">Chiropractor</span></div>
  </section>

  <section class="card card--back-light">
    <div class="brand-mark"></div>
    <div class="brand-name">Marwick</div>
    <div class="brand-line">Family Chiropractic</div>
    <div class="web">www.marwickspine.example</div>
  </section>

  <section class="card card--back-brown">
    <div class="brand-name">Marwick</div>
    <div class="brand-line">Family Chiropractic</div>
    <div class="web">www.marwickspine.example</div>
  </section>

  <section class="card card--back-black">
    <div class="brand-mark"></div>
    <div class="brand-name">Marwick</div>
    <div class="brand-line">Family Chiropractic</div>
    <div class="web">www.marwickspine.example</div>
  </section>
</body>
</html>
```